Modernize Police Fraternity Website

We're in search of a web developer to rejuvenate the digital presence of our co-ed fraternity at Ferndale Ridge State, which is dedicated to supporting students pursuing careers in criminal justice and law enforcement. We aim for a modern, minimalist website that's both user-friendly and simple to maintain. Key features will include an inviting landing page, an easy-to-use contact form, and a secure online store for handling memberships, donations, and sales of items like t-shirts. While we're eager to retain as much of our existing content as possible, we're also open to thoughtful content adjustments to elevate our design. For a glimpse of our current website and to understand our mission, please visit taurhokappa.org.

Target Market(s)

Students

Coding

Coded - Design and coding required

Number of Pages Required

4 page

Font styles to use
Serif

Colors

Designer to choose colors to be used in the design.

Requirements
Must have
• Landing page, contact us, shop
Nice to have
• membership tracking

```html
<!DOCTYPE html>
<html lang="en">
<head>
<meta charset="utf-8">
<title>Tau Rho Kappa Fraternity</title>
<link href="https://fonts.googleapis.com/css2?family=Poppins:wght@400;500;600;700&family=Mrs+Saint+Delafield&display=swap" rel="stylesheet">
<style>
:root{
  --red:#7b1a0b;
  --red-text:#8a1c0c;
  --tan:#b9b6a2;
  --stone:#bdbbac;
  --ink:#1d1d1d;
  --white:#ffffff;
  --footer:#565453;
  --footer-base:#6b6360;
  --card-shadow:0 6px 18px rgba(0,0,0,.10);
}
*{margin:0;padding:0;box-sizing:border-box}
html,body{width:1200px;height:4454px;overflow:hidden}
body{position:relative;font-family:"Poppins",sans-serif;color:var(--ink);background:var(--white)}
.abs{position:absolute}
.photo{position:absolute}

/* hero */
.hero{left:0;top:0;width:1200px;height:654px;background:linear-gradient(180deg,#2f5f9c 0%,#5d84b5 35%,#8a7a62 60%,#3d4a2a 85%,#2d3a22 100%)}
.brand-badge{left:86px;top:0;width:144px;height:142px;background:var(--white);border-radius:0 0 72px 72px;display:flex;flex-direction:column;align-items:center;justify-content:center;gap:6px}
.brand-badge .dot{width:22px;height:22px;border-radius:50%;background:var(--red)}
.brand-badge span{font-size:14px;font-weight:600;color:var(--red);text-align:center;line-height:1.15}
.nav{left:391px;top:52px;display:flex;gap:26px;font-size:15px;color:var(--white)}
.nav a{color:inherit;text-decoration:none}
.nav a.active{color:#e2503a}
.nav-rule{left:230px;top:100px;width:856px;height:1px;background:rgba(255,255,255,.7)}
.btn{position:absolute;display:flex;align-items:center;justify-content:center;border-radius:30px;font-size:14px;text-decoration:none}
.btn-red{background:var(--red);color:var(--white)}
.btn-tan{background:var(--tan);color:var(--red)}
.hero-title{left:0;top:432px;width:1200px;text-align:center;color:var(--white);font-size:55px;font-weight:600;text-shadow:0 3px 8px rgba(0,0,0,.4)}
.hero-sub{left:0;top:522px;width:1200px;text-align:center;color:var(--white);font-size:25px;font-weight:500}

/* social bar */
.social-title{left:126px;top:708px;font-size:19px;font-weight:600;color:var(--red-text)}
.social-item{top:703px;display:flex;align-items:center;gap:8px;font-size:16px}
.social-item i{display:block;width:34px;height:34px;border-radius:4px;background:var(--red)}

/* about */
.about{left:0;top:787px;width:1200px;height:813px;background:var(--red)}
.eyebrow{font-size:15px}
.about .eyebrow{left:130px;top:64px;color:#e9d6d0}
.about h2{position:absolute;left:130px;top:98px;width:285px;font-size:35px;font-weight:600;line-height:57px;white-space:nowrap;color:var(--white)}
.about p{position:absolute;left:436px;top:76px;width:632px;font-size:13px;line-height:20.6px;color:var(--white)}
.about-photo{left:126px;top:335px;width:937px;height:478px;border-radius:24px 24px 0 0;background:linear-gradient(180deg,#5a4a3a 0%,#3b3330 50%,#2a2426 100%)}
.dots{left:560px;top:766px;display:flex;gap:6px}
.dots i{width:16px;height:16px;border-radius:50%;background:var(--white)}

/* support */
.support-photo{left:0;top:1662px;width:576px;height:477px;border-radius:0 30px 30px 0;background:linear-gradient(160deg,#9a7a5e 0%,#b4aea8 50%,#8c8884 100%)}
.secure{left:504px;top:1942px;width:144px;height:144px;border-radius:50%;background:var(--red);border:4px solid var(--white);box-shadow:0 6px 16px rgba(0,0,0,.3);display:flex;flex-direction:column;align-items:center;justify-content:center;color:var(--white);font-size:13px;line-height:14px;text-align:center}
.secure .lock{width:34px;height:34px;border-radius:50%;background:#a52612;margin-bottom:8px;display:flex;align-items:center;justify-content:center}
.support .eyebrow{left:688px;top:1776px;color:var(--red-text)}
.support h2{position:absolute;left:688px;top:1810px;font-size:38px;font-weight:600}
.accent{color:var(--red-text)}
.support p{position:absolute;left:688px;top:1886px;width:370px;font-size:15px;line-height:32px}
.next{left:1012px;top:2034px;display:flex;align-items:center;gap:8px;font-size:12px}

/* alumni banner */
.banner-back{left:126px;top:2262px;width:1074px;height:435px;background:var(--stone);border-radius:0 0 0 30px}
.banner-photo{left:81px;top:2218px;width:1036px;height:439px;border-radius:30px 0 0 30px;background:linear-gradient(180deg,#5d5a5c 0%,#6e6b6c 45%,#4b4849 100%)}
.banner-title{left:81px;top:2408px;width:1036px;text-align:center;font-size:46px;font-weight:600;color:var(--white)}
.banner-title .accent{color:#e0321c}

/* careers */
.careers-title{left:0;top:2800px;width:1200px;text-align:center;font-size:38px;font-weight:600}
.card{position:absolute;width:304px;background:var(--white);border-radius:12px;box-shadow:var(--card-shadow);display:flex;flex-direction:column;align-items:center;justify-content:center;gap:14px;text-align:center;font-size:19px;font-weight:500;line-height:28px}
.card svg{width:44px;height:44px}

/* welcome alumni */
.alumni{left:0;top:3377px;width:1200px;height:667px;background:var(--red);color:var(--white)}
.alumni .eyebrow{left:126px;top:96px}
.alumni h2{position:absolute;left:126px;top:124px;font-size:40px;font-weight:600}
.alumni p{position:absolute;left:126px;top:205px;width:480px;font-size:15px;line-height:32px}
.signature{left:126px;top:440px;font-family:"Mrs Saint Delafield",cursive;font-size:28px;line-height:35px;color:#e9d6d0}
.alumni-photo{left:716px;top:69px;width:484px;height:538px;border-radius:40px 0 0 0;background:linear-gradient(180deg,#3f7fc9 0%,#8fb3d8 35%,#7a6e62 70%,#4a3f38 100%)}
.alumni-circle{left:634px;top:406px;width:198px;height:198px;border-radius:50%;border:4px solid var(--white);background:linear-gradient(180deg,#3b5ba8 0%,#6b7aa0 60%,#3a3440 100%)}

/* footer */
.footer{left:0;top:4044px;width:1200px;height:348px;background:var(--footer);color:var(--white);text-align:center}
.footer-brand{left:0;top:50px;width:1200px;display:flex;flex-direction:column;align-items:center;gap:8px;font-size:17px;font-weight:600;color:#e3b9ad}
.footer-brand .dot{width:40px;height:40px;border-radius:50%;background:var(--red)}
.footer-social{left:0;top:162px;width:1200px;display:flex;justify-content:center;gap:22px}
.footer-social i{width:28px;height:28px;border-radius:4px;background:#a52612}
.footer-nav{left:0;top:220px;width:1200px;display:flex;justify-content:center;gap:34px;font-size:14px}
.footer-line{left:0;width:1200px;font-size:14px}
.base{left:0;top:4392px;width:1200px;height:62px;background:var(--footer-base);color:var(--white);font-size:12px;display:flex;align-items:center;justify-content:center}
</style>
</head>
<body>

<section class="hero abs photo" role="img" aria-label="Photo of a historic campus tower building against a blue sky with palm trees and gardens"></section>
<div class="brand-badge abs"><div class="dot"></div><span>Tau Rho<br>Kappa</span></div>
<nav class="nav abs"><a class="active">Home</a><a>About Us</a><a>Join Us</a><a>Events</a><a>Alumni</a></nav>
<div class="nav-rule abs"></div>
<a class="btn btn-red" style="left:922px;top:42px;width:143px;height:41px">Donate Now</a>
<h1 class="hero-title abs">Tau Rho Kappa Fraternity</h1>
<div class="hero-sub abs">~Est 1935~</div>

<div class="social-title abs">Visit ΤΡΚ on Social Media!</div>
<div class="social-item abs" style="left:446px"><i></i>Friendbook</div>
<div class="social-item abs" style="left:607px"><i></i>Chirper</div>
<div class="social-item abs" style="left:768px"><i></i>WorkLink</div>
<div class="social-item abs" style="left:928px"><i></i>Snapgram</div>

<section class="about abs">
  <div class="eyebrow abs">About Us</div>
  <h2>Welcome to<br>Tau Rho Kappa!</h2>
  <a class="btn btn-tan" style="left:130px;top:226px;width:157px;height:50px">Read More</a>
  <p>Tau Rho Kappa is the coeducational professional criminal justice fraternity at the acclaimed Ferndale Ridge State University in beautiful Ferndale Ridge, California.<br><br>Student members are individuals, of varying majors, with career goals in the criminal justice system such as law enforcement, probation, corrections, security, and law. The primary objectives of the Fraternity are to assist members with occupational preparation, career selection, career acquisition and to provide a fertile environment for academic study. Tau Rho Kappa also supports and promotes the Department of Justice Studies, strives to improve the campus environment, and makes positive contributions to the local community. Learn more about us!</p>
  <div class="about-photo photo" role="img" aria-label="Group photo of fraternity members in business attire"></div>
  <div class="dots abs"><i></i><i></i><i></i><i></i></div>
</section>

<section class="support">
  <div class="support-photo photo" role="img" aria-label="Smiling members wearing grey fraternity sweatshirts"></div>
  <div class="secure abs"><div class="lock"><svg width="14" height="16" viewBox="0 0 14 16"><rect x="1" y="7" width="12" height="9" rx="1.5" fill="#fff"/><path d="M4 7V5a3 3 0 0 1 6 0v2" stroke="#fff" stroke-width="2" fill="none"/></svg></div>Secure<br>Donation</div>
  <div class="eyebrow abs">Help Us</div>
  <h2>Support Our <span class="accent">ΤΡΚ</span></h2>
  <p>Help our organization by donating today! All donations go directly to making a difference for our cause.</p>
  <a class="btn btn-red" style="left:688px;top:2016px;width:156px;height:52px;font-size:15px">Donate Now</a>
  <div class="next abs"><svg width="26" height="10" viewBox="0 0 26 10"><path d="M0 5h24M19 1l5 4-5 4" stroke="#1d1d1d" stroke-width="1.4" fill="none"/></svg>Next</div>
</section>

<div class="banner-back abs"></div>
<div class="banner-photo photo" role="img" aria-label="Black and white photo of uniformed officers standing in rows"></div>
<div class="banner-title abs">Our Alumni Are <span class="accent">Special Agents</span></div>

<h2 class="careers-title abs">ΤΡΚ Criminal Justice <span class="accent">Alumni Careers</span></h2>
<div class="card" style="left:126px;top:2884px;height:175px"><svg viewBox="0 0 44 44"><path d="M10 26v-6a12 12 0 0 1 24 0v6" stroke="#8a1c0c" stroke-width="3.5" fill="none"/><rect x="7" y="24" width="7" height="10" rx="2" fill="#8a1c0c"/><rect x="30" y="24" width="7" height="10" rx="2" fill="#8a1c0c"/></svg>Special Agent</div>
<div class="card" style="left:448px;top:2884px;height:175px"><svg viewBox="0 0 44 44"><path d="M22 4l15 6v10c0 10-7 16-15 20C14 36 7 30 7 20V10z" stroke="#8a1c0c" stroke-width="3.5" fill="none"/><rect x="16" y="20" width="12" height="9" rx="1.5" fill="#8a1c0c"/><path d="M18 20v-3a4 4 0 0 1 8 0v3" stroke="#8a1c0c" stroke-width="2.5" fill="none"/></svg>Private Security/<br>Intelligence</div>
<div class="card" style="left:768px;top:2884px;height:175px"><svg viewBox="0 0 44 44"><path d="M22 8v28M10 12h24M14 36h16" stroke="#8a1c0c" stroke-width="3"/><path d="M10 12l-5 10h10zM34 12l-5 10h10z" fill="#8a1c0c"/></svg>Lawyer</div>
<div class="card" style="left:126px;top:3090px;height:173px"><svg viewBox="0 0 44 44"><circle cx="22" cy="14" r="9" stroke="#8a1c0c" stroke-width="3.5" fill="none"/><path d="M9 40a13 13 0 0 1 26 0z" fill="#8a1c0c"/></svg>Probation/Parole</div>
<div class="card" style="left:448px;top:3090px;height:173px"><svg viewBox="0 0 44 44"><path d="M22 6v32M8 12h28M12 38h20" stroke="#8a1c0c" stroke-width="3"/><path d="M8 12l-5 11h10zM36 12l-5 11h10z" stroke="#8a1c0c" stroke-width="2.5" fill="none"/></svg>Local/State Law<br>Enforcement</div>
<div class="card" style="left:768px;top:3090px;height:173px"><svg viewBox="0 0 44 44"><rect x="10" y="20" width="24" height="18" rx="2" fill="#8a1c0c"/><path d="M16 8h12l-3 12h-6z" fill="#8a1c0c"/></svg>DA Investigator</div>

<section class="alumni abs">
  <div class="eyebrow abs">Welcome to</div>
  <h2>Alumni</h2>
  <p>I want to welcome you to the new Tau Rho Kappa Fraternity website. The public section is primarily for the use of the active Fraternity members to help them recruit new members and make available their calendar of events. The Alumni section is only available to active alumni with good standing. We welcome comments and suggestions on other topics to be included and on ways to improve our website.</p>
  <div class="signature abs">Daniel Moreno<br>Alumni President</div>
  <a class="btn btn-tan" style="left:126px;top:536px;width:158px;height:53px;font-size:15px;color:#fff">Read more</a>
  <div class="alumni-photo photo" role="img" aria-label="Group of members celebrating on a hilltop under a blue sky"></div>
  <div class="alumni-circle photo" role="img" aria-label="Older group photo of alumni in suits"></div>
</section>

<footer class="footer abs">
  <div class="footer-brand abs"><div class="dot"></div>Tau Rho Kappa</div>
  <div class="footer-social abs"><i></i><i></i><i></i><i></i></div>
  <div class="footer-nav abs"><span>Home</span><span>About Us</span><span>Join Us</span><span>Events</span><span>Alumni</span></div>
  <div class="footer-line abs" style="top:260px">Email Us: info@taurhokappa.org</div>
  <div class="footer-line abs" style="top:298px">Visit Us: 418 West Orchard Avenue Ferndale Ridge, California</div>
</footer>
<div class="base abs">© 2023-2024 taurhokappa</div>

</body>
</html>
```